Sparrow Haulage needs a business card design.

Design a double-sided business card for new freight business. On the front, would like to see our logo along with the following info:

Martin Obuya
CEO/FOUNDER
555-206-7142
martinobuya@sparrow-haulage.example

On the reverse side, we would like to use the graphic image of our logo only without the Sparrow Haulage name.

```html
<!DOCTYPE html>
<html lang="en">
<head>
<meta charset="utf-8">
<title>Sparrow Haulage – Business Card</title>
<link href="https://fonts.googleapis.com/css2?family=Arimo:wght@400;700&display=swap" rel="stylesheet">
<style>
  :root {
    --backdrop: #9c9c9c;
    --paper: #ffffff;
    --navy: #14145e;
    --navy-deep: #06005a;
    --red: #c00a0a;
    --red-bright: #b80000;
    --ink: #2b2b2b;
    --rule: #8a8a8a;
    --pale: #ece8f2;
  }
  * { margin: 0; padding: 0; box-sizing: border-box; }
  html, body {
    width: 1200px; height: 1200px; overflow: hidden;
    background: var(--backdrop);
    font-family: "Arimo", Arial, sans-serif;
  }
  .stage { position: relative; width: 1200px; height: 1200px; }

  .card {
    position: absolute; top: 303px;
    width: 368px; height: 594px;
  }

  /* Reverse side */
  .card-back {
    left: 201px;
    background: linear-gradient(180deg, var(--red-bright) 0%, #8a0020 40%, #3e0040 70%, var(--navy-deep) 100%);
  }
  .back-brand {
    position: absolute; left: 34px; top: 474px;
    display: flex; align-items: center; gap: 14px;
  }
  .back-brand .brand-square {
    width: 40px; height: 40px; background: var(--pale);
  }
  .back-wordmark {
    color: var(--pale);
    font-weight: 700; font-size: 34px; line-height: 36px;
    letter-spacing: 9px; text-transform: uppercase;
  }

  /* Front side */
  .card-front {
    left: 599px; width: 364px;
    background: var(--paper);
    text-align: center;
  }
  .brand {
    position: absolute; left: 0; right: 0; top: 150px;
    display: flex; align-items: center; justify-content: center; gap: 14px;
  }
  .brand .brand-square { width: 42px; height: 42px; background: var(--red); }
  .brand-name {
    color: var(--navy);
    font-weight: 700; font-size: 25px; line-height: 28px;
    letter-spacing: 3px; text-transform: uppercase; text-align: left;
  }

  .person-name {
    position: absolute; left: 0; right: 0; top: 376px;
    font-weight: 700; font-size: 22px; color: var(--navy);
  }
  .person-name .surname { color: var(--red); }
  .person-role {
    position: absolute; left: 0; right: 0; top: 404px;
    font-size: 17px; color: var(--ink);
  }

  .contact-icons {
    position: absolute; left: 0; right: 0; top: 438px;
    display: flex; align-items: center; justify-content: center; gap: 4px;
  }
  .contact-icons .rule { width: 52px; height: 1px; background: var(--rule); margin: 0 4px; }
  .icon-box {
    width: 25px; height: 25px; border-radius: 3px; background: var(--red);
    display: flex; align-items: center; justify-content: center;
  }
  .icon-box svg { width: 17px; height: 17px; }

  .contact-lines {
    position: absolute; left: 0; right: 0; top: 478px;
    font-size: 16px; line-height: 22px; color: var(--ink);
  }
  .contact-lines .email { font-size: 15px; }
  .contact-lines .web-a { color: var(--navy); }
  .contact-lines .web-b { color: var(--red); }
</style>
</head>
<body>
<main class="stage">

  <section class="card card-back" aria-label="Card reverse side">
    <div class="back-brand">
      <span class="brand-square" aria-hidden="true"></span>
      <div class="back-wordmark">Sparrow<br>Haulage</div>
    </div>
  </section>

  <section class="card card-front" aria-label="Card front side">
    <div class="brand">
      <span class="brand-square" aria-hidden="true"></span>
      <span class="brand-name">Sparrow<br>Haulage</span>
    </div>

    <h1 class="person-name">MARTIN <span class="surname">OBUYA</span></h1>
    <p class="person-role">CEO/FOUNDER</p>

    <div class="contact-icons">
      <span class="rule"></span>
      <span class="icon-box" aria-label="Phone">
        <svg viewBox="0 0 24 24" fill="none" stroke="#fff" stroke-width="2" stroke-linejoin="round">
          <path d="M3 9c0-3 4-5 9-5s9 2 9 5l-1 2h-4l-1-3H9L8 11H4z"/>
          <rect x="6" y="13" width="12" height="7" rx="1"/>
        </svg>
      </span>
      <span class="icon-box" aria-label="Email">
        <svg viewBox="0 0 24 24" fill="none" stroke="#fff" stroke-width="2">
          <rect x="3" y="5" width="18" height="14"/>
          <path d="M3 5l9 8 9-8M3 19l7-6M21 19l-7-6"/>
        </svg>
      </span>
      <span class="icon-box" aria-label="Website">
        <svg viewBox="0 0 24 24" fill="none" stroke="#fff" stroke-width="2">
          <circle cx="12" cy="12" r="9"/>
          <path d="M3 12h18M12 3c3 3 3 15 0 18M12 3c-3 3-3 15 0 18"/>
        </svg>
      </span>
      <span class="rule"></span>
    </div>

    <div class="contact-lines">
      <p class="phone">555-206-7142</p>
      <p class="email">martinobuya@sparrow-haulage.example</p>
      <p class="web">www.<span class="web-a">sparrow</span>-<span class="web-b">haulage</span>.example</p>
    </div>
  </section>

</main>
</body>
</html>
```